Poster - gross für Messestand VORALIS
Zielgruppe
Wir sind ein junges Beratungs- und Softwareentwicklungsunternehmen für Business Analytics & Big-Data Lösungen (Mathematiker). Business Analytics ist ein interdisziplinäres Gebiet, mit dem Ziel unternehmerische Entscheidungen und Prozesse durch die kombinierte Anwendung von detaillierten Datenanalysen, Wahrscheinlichkeitsprozessen, Optimierungsmodelle und die Nutzung von modernsten IT Technologien zu optimieren.
Zielgruppe aus der Messe: Marketingleiter, Entscheider grosser E-commerce Unternehmen, die entscheiden müssen, wo Sie das Marketing Budget am effektivsten invenstieren
Produkt: Convertion Atrribution siehe case study http://www.kordwig-tln.example/projects_de.html
Image der Firma: Jung, erfolgreich, Mathematiker, absulut professionell, innovative, sehr international
Messestand: Standart, weisse Wände, grauer Teppich,
Aufgabenstellung
Poster soll als Hintergrund eines Messestandes sein. Es soll ein Hingucker mit ansprechendem Fototeil sein und Leiste mit mainpoints.
zum Beispiel eine Idee:
Bild: Bernhard Quellmar oder jemand, der für verrückten, innovative, creative denkenden Intelektueller steht ( Mathematiker?) und bekannt ist? Offen fúr Ideen!
Slogan ( bei Bernhard Quellmar z.B.): Success is not relative!
Text:
Kordwig TLN your Business Analytics partner, providing you with state-of-the-art Business Analytics & Big Data solutions for:
- conversion attribution
- mixed-media models
- individual customer offer
- churn reduction strategies
- data mining
- demand forecasting
Masse mindestens DINA 0 am leibesten grösser 1,50 x 2m

```html
<!DOCTYPE html>
<html lang="en">
<head>
<meta charset="utf-8">
<title>Kordwig TLN – Trade Fair Poster</title>
<link rel="stylesheet" href="https://fonts.googleapis.com/css2?family=Open+Sans:wght@600;700&family=Cabin:wght@400;500&display=swap">
<style>
  :root {
    --poster-white: #ffffff;
    --ink: #2b2b2b;
    --accent-red: #d0232b;
    --accent-red-dark: #b51a22;
    --photo-brick: #8a4a3e;
    --photo-stone: #a7a29a;
    --photo-door: #3b3d45;
    --photo-pavement: #bdb6ab;
    --frame: #cfcfcf;
  }
  * { box-sizing: border-box; margin: 0; padding: 0; }
  html, body {
    width: 900px; height: 1200px; overflow: hidden;
    background: var(--poster-white);
  }
  .poster {
    position: relative;
    width: 900px; height: 1200px;
    background: var(--poster-white);
    border: 1px solid var(--frame);
    overflow: hidden;
    font-family: "Cabin", "Candara", sans-serif;
    color: var(--ink);
  }
  .hero {
    position: absolute; left: 0; top: 0;
    width: 900px; height: 600px;
    background:
      linear-gradient(180deg, rgba(0,0,0,0.05) 0%, rgba(0,0,0,0) 40%, rgba(0,0,0,0.15) 100%),
      linear-gradient(90deg,
        var(--photo-brick) 0%, #9b6457 17%,
        var(--photo-stone) 26%, #c4bfb6 38%,
        var(--photo-door) 48%, var(--photo-door) 74%,
        #d8d4cc 80%, #cbc6bd 100%);
  }
  .hero-ground {
    position: absolute; left: 0; bottom: 0;
    width: 100%; height: 260px;
    background: linear-gradient(180deg, var(--photo-pavement) 0%, #aaa397 70%, #8f897f 100%);
  }
  .hero-headline,
  .hero-tagline {
    position: absolute; left: 0; width: 100%;
    text-align: center;
    font-family: "Open Sans", "Segoe UI", sans-serif;
    color: var(--poster-white);
    text-shadow: 0 1px 3px rgba(0,0,0,0.25);
  }
  .hero-headline {
    top: 18px;
    font-size: 45px; font-weight: 700; letter-spacing: 0.2px;
  }
  .hero-tagline {
    top: 516px;
    font-size: 47px; font-weight: 600;
  }
  .offer {
    position: absolute; left: 50px; top: 650px;
  }
  .offer-intro {
    font-size: 35px; font-weight: 400;
    color: #333;
    margin-bottom: 20px;
  }
  .offer-list { list-style: none; padding-left: 22px; }
  .offer-list li {
    position: relative;
    padding-left: 35px;
    font-size: 28px; line-height: 41px;
    color: #333;
  }
  .offer-list li::before {
    content: "";
    position: absolute; left: 0; top: 14px;
    width: 13px; height: 13px;
    background: linear-gradient(135deg, var(--accent-red), var(--accent-red-dark));
  }
  .brand {
    position: absolute; left: 400px; top: 1062px;
    display: flex; align-items: center; gap: 14px;
  }
  .brand-name {
    font-size: 44px; font-weight: 500;
    color: #111;
    letter-spacing: 0.5px;
  }
  .brand-square {
    width: 34px; height: 34px;
    background: var(--accent-red);
  }
  .stripes { position: absolute; left: 0; top: 0; }
</style>
</head>
<body>
  <div class="poster">
    <div class="hero" role="img" aria-label="Photograph of a red child's tricycle chained to a concrete post on a city sidewalk in front of a brick wall and a grey door">
      <div class="hero-ground"></div>
    </div>
    <h1 class="hero-headline">Success is NOT a matter of luck.</h1>
    <p class="hero-tagline">Make Smarter Decisions!</p>

    <section class="offer">
      <h2 class="offer-intro">Your Business Analytics partner for:</h2>
      <ul class="offer-list">
        <li>Conversion Attribution</li>
        <li>Data Mining / Customer Classification</li>
        <li>360° Analysis</li>
        <li>Profit-Max SEA Bidding</li>
        <li>Call Center Staffing Tool</li>
        <li>Data Analysis Service</li>
        <li>Decision Support Tools</li>
      </ul>
    </section>

    <div class="brand">
      <span class="brand-name">Kordwig TLN</span>
      <span class="brand-square"></span>
    </div>

    <svg class="stripes" width="900" height="1200" viewBox="0 0 900 1200" aria-hidden="true">
      <rect x="0" y="1138" width="350" height="13" fill="var(--accent-red)"/>
      <rect x="0" y="1160" width="350" height="13" fill="var(--accent-red)"/>
      <rect x="0" y="1182" width="900" height="18" fill="var(--accent-red)"/>
    </svg>
  </div>
</body>
</html>
```